Political Mail Out Beltran front and back

Front
Tomas (Study Hall) Beltran!

What's that famous saying?

Show me who your friends are and I'll tell you who you really are!
(show the two guys)

Dennis Ocampo is charged with voter fraud by changing voter addresses from across the RGV so they could vote in Edinburg
Back
Did Tomas (Study Hall) Beltran commit voter fraud when he ran for office in 2016?
(insert blurred photo)

Here is a list of people from all over the RGV that voted in Edinburg in the 2016 race.
Here is a break down:

(highlight the number and where they were first registered to vote)

9 People voted in Edinburg who were registered in Donna.
13 People voted in Edinburg who were registered in San Juan
8 People voted in Edinburg who were registered in Pharr
31 People voted in Edinburg who were registered in McAllen
2 People voted in Edinburg who were registered in La Joya
6 People voted in Edinburg who were registered in Edcouch
2 People voted in Edinburg who were registered in Mercedes
2 People voted in Edinburg who were registered in Monte Alto
6 People voted in Edinburg who were registered in Weslaco
1 Person voted in Edinburg who were registered in Penitas
3 People voted in Edinburg who were registered in Alamo
5 People voted in Edinburg who were registered in Elsa
6 People voted in Edinburg who were registered in Mission
1 Person voted in Edinburg who were registered in Alton

Will Tomas (Study Hall) Beltran CHEAT in 2020?

Only time will tell.

Vote Tomas (Study Hall) Beltran OUT of office.

```html
<!DOCTYPE html>
<html lang="en">
<head>
<meta charset="utf-8">
<title>Beltran Mail Out – Front and Back</title>
<link href="https://fonts.googleapis.com/css2?family=Montserrat:wght@400;600;700;800;900&family=Oswald:wght@700&display=swap" rel="stylesheet">
<style>
  :root{
    --board:#d6d6d6;
    --navy:#1b2d7a;
    --navy-deep:#0f1c5c;
    --sky:#14aee6;
    --sky-deep:#0c8fd0;
    --red:#c00812;
    --red-deep:#8f0008;
    --dark-red:#a80a10;
    --yellow:#fff200;
    --white:#ffffff;
    --silver:#cfd3d8;
    --ink:#333333;
    --stripe:#e9e9ea;
    --charcoal:#232323;
    --photo-a:#3a3a3a;
    --photo-b:#9a9a9a;
  }
  *{margin:0;padding:0;box-sizing:border-box}
  html,body{width:1200px;height:838px;overflow:hidden}
  body{
    background:linear-gradient(180deg,#dedede 0%,var(--board) 70%,#a9a9a9 100%);
    font-family:"Montserrat",Arial,sans-serif;
    position:relative;
  }
  .side-label{position:absolute;top:38px;font-size:14px;color:#333;letter-spacing:.5px}
  .side-label.front{left:56px}
  .side-label.back{left:636px}

  .panel{position:absolute;top:61px;width:533px;height:753px;background:var(--white);overflow:hidden}
  .panel--front{left:46px}
  .panel--back{left:629px}
  .panel-shapes{position:absolute;inset:0}

  .centered{position:absolute;left:0;right:0;text-align:center;white-space:nowrap}

  /* FRONT */
  .front-name{font-weight:900;line-height:1;letter-spacing:-1px}
  .front-name.first{top:16px;font-size:74px;color:var(--sky)}
  .front-name.grade{top:90px;font-size:46px;color:var(--silver);text-shadow:0 2px 3px rgba(0,0,0,.45)}
  .front-name.last{top:140px;font-size:68px;color:var(--sky)}
  .saying{font-weight:900;color:var(--dark-red);line-height:1;font-size:46px;letter-spacing:-1px}
  .saying.one{top:242px}
  .saying.two{top:291px;font-size:47px}
  .friends-line{top:370px;color:var(--white);font-weight:800;font-size:21.5px;line-height:28px;text-shadow:0 2px 2px rgba(0,0,0,.45)}
  .friends-photo{position:absolute;left:0;top:430px;width:533px;height:238px;
    background:radial-gradient(ellipse at 55% 60%,var(--photo-b) 0%,#6b6b6b 45%,var(--photo-a) 100%)}
  .charge-name{top:676px;font-weight:800;font-size:25px;color:var(--white);letter-spacing:-.5px}
  .charge-text{top:708px;font-weight:600;font-size:13.5px;line-height:18px;color:var(--white)}

  /* BACK */
  .back-title{font-family:"Oswald",Impact,sans-serif;font-weight:700;line-height:1;text-shadow:0 3px 3px rgba(0,0,0,.35)}
  .back-title.one{top:20px;font-size:50px;color:var(--white)}
  .back-title.one .hl{color:var(--yellow)}
  .back-title.two{top:76px;font-size:52px;color:var(--yellow)}
  .back-question{top:136px;font-weight:800;font-size:21px;line-height:29px;color:var(--white)}
  .back-intro{top:227px;font-weight:700;font-size:16px;line-height:22px;color:var(--white)}

  .breakdown{position:absolute;left:38px;top:297px;width:462px;list-style:none}
  .breakdown li{height:22px;display:flex;align-items:center;font-size:13.5px;white-space:nowrap}
  .breakdown li:nth-child(even){background:var(--stripe)}
  .breakdown .count{width:125px;padding-left:3px;color:var(--navy);font-weight:700}
  .breakdown .middle{width:243px;color:var(--ink);font-weight:400;font-size:12.5px}
  .breakdown .town{color:var(--red);font-weight:700;font-size:13px}

  .cheat-line{top:628px;font-weight:800;font-size:18.5px;color:var(--white);letter-spacing:-.3px}
  .time-line{top:678px;font-weight:800;font-size:15px;color:var(--yellow)}
  .vote-out{top:701px;font-weight:900;font-size:20.5px;line-height:25px;color:var(--white)}
</style>
</head>
<body>
  <div class="side-label front">FRONT</div>
  <div class="side-label back">BACK</div>

  <section class="panel panel--front">
    <svg class="panel-shapes" width="533" height="753" viewBox="0 0 533 753">
      <defs>
        <radialGradient id="frontBlue" cx="50%" cy="45%" r="70%">
          <stop offset="0" stop-color="#2a45a3"/>
          <stop offset="1" stop-color="#0f1c5c"/>
        </radialGradient>
        <linearGradient id="frontRed" x1="0" y1="0" x2="0" y2="1">
          <stop offset="0" stop-color="#c00812"/>
          <stop offset="1" stop-color="#8f0008"/>
        </linearGradient>
        <linearGradient id="frontSky" x1="0" y1="0" x2="0" y2="1">
          <stop offset="0" stop-color="#14aee6"/>
          <stop offset="1" stop-color="#0c8fd0"/>
        </linearGradient>
      </defs>
      <path d="M0 0H533V188Q266 244 0 188Z" fill="url(#frontBlue)"/>
      <path d="M0 195Q266 251 533 195" fill="none" stroke="#c9c9c9" stroke-width="3"/>
      <path d="M0 430V399L30 358Q36 350 48 350H485Q497 350 503 358L533 399V430Z" fill="url(#frontRed)"/>
      <rect x="0" y="668" width="533" height="85" fill="url(#frontSky)"/>
    </svg>

    <div class="centered front-name first">TOMAS</div>
    <div class="centered front-name grade">(STUDY HALL)</div>
    <div class="centered front-name last">BELTRAN!</div>

    <div class="centered saying one">WHAT'S THAT</div>
    <div class="centered saying two">FAMOUS SAYING?</div>

    <div class="centered friends-line">SHOW ME WHO YOUR FRIENDS ARE AND<br>I'LL TELL YOU WHO YOU REALLY ARE!</div>

    <div class="friends-photo" role="img" aria-label="Black and white photo of the candidate and Dennis Ocampo smiling side by side"></div>

    <div class="centered charge-name">DENNIS OCAMPO</div>
    <div class="centered charge-text">is charged with voter fraud by changing voter addresses from<br>across the RGV so they could vote in Edinburg</div>
  </section>

  <section class="panel panel--back">
    <svg class="panel-shapes" width="533" height="753" viewBox="0 0 533 753">
      <defs>
        <radialGradient id="backRed" cx="50%" cy="35%" r="70%">
          <stop offset="0" stop-color="#d3101a"/>
          <stop offset="1" stop-color="#8f0008"/>
        </radialGradient>
        <linearGradient id="backSky" x1="0" y1="0" x2="0" y2="1">
          <stop offset="0" stop-color="#14aee6"/>
          <stop offset="1" stop-color="#0c8fd0"/>
        </linearGradient>
      </defs>
      <rect x="0" y="0" width="533" height="753" fill="#f6f6f7"/>
      <path d="M44 187L487 187L455 271Q451 281 440 281H93Q82 281 78 271Z" fill="#1b2d7a"/>
      <path d="M0 0H533V168Q266 254 0 168Z" fill="url(#backRed)"/>
      <path d="M0 174Q266 260 533 174" fill="none" stroke="#e3e3e3" stroke-width="3"/>
      <rect x="0" y="620" width="533" height="41" fill="url(#backSky)"/>
      <rect x="0" y="661" width="533" height="92" fill="#232323"/>
    </svg>

    <div class="centered back-title one"><span class="hl">TOMAS</span> (STUDY HALL)</div>
    <div class="centered back-title two">BELTRAN!</div>
    <div class="centered back-question">COMMIT VOTER FRAUD WHEN HE<br>RAN FOR OFFICE IN 2016?</div>
    <div class="centered back-intro">Here is a list of people from all over the RGV<br>that voted in Edinburg in the 2016 race.</div>

    <ul class="breakdown">
      <li><span class="count">9 People voted</span><span class="middle">in Edinburg who were registered in</span><span class="town">DONNA</span></li>
      <li><span class="count">13 People voted</span><span class="middle">in Edinburg who were registered in</span><span class="town">SAN JUAN</span></li>
      <li><span class="count">8 People voted</span><span class="middle">in Edinburg who were registered in</span><span class="town">PHARR</span></li>
      <li><span class="count">31 People voted</span><span class="middle">in Edinburg who were registered in</span><span class="town">MCALLEN</span></li>
      <li><span class="count">2 People voted</span><span class="middle">in Edinburg who were registered in</span><span class="town">LA JOYA</span></li>
      <li><span class="count">6 People voted</span><span class="middle">in Edinburg who were registered in</span><span class="town">EDCOUCH</span></li>
      <li><span class="count">2 People voted</span><span class="middle">in Edinburg who were registered in</span><span class="town">MERCEDES</span></li>
      <li><span class="count">2 People voted</span><span class="middle">in Edinburg who were registered in</span><span class="town">MONTE ALTO</span></li>
      <li><span class="count">6 People voted</span><span class="middle">in Edinburg who were registered in</span><span class="town">WESLACO</span></li>
      <li><span class="count">1 People voted</span><span class="middle">in Edinburg who were registered in</span><span class="town">PENITAS</span></li>
      <li><span class="count">3 People voted</span><span class="middle">in Edinburg who were registered in</span><span class="town">ALAMO</span></li>
      <li><span class="count">5 People voted</span><span class="middle">in Edinburg who were registered in</span><span class="town">ELSA</span></li>
      <li><span class="count">6 People voted</span><span class="middle">in Edinburg who were registered in</span><span class="town">MISSION</span></li>
      <li><span class="count">1 People voted</span><span class="middle">in Edinburg who were registered in</span><span class="town">ALTON</span></li>
    </ul>

    <div class="centered cheat-line">Will Tomas (Study Hall) Beltran CHEAT in 2020?</div>
    <div class="centered time-line">ONLY TIME WILL TELL</div>
    <div class="centered vote-out">VOTE TOMAS (STUDY HALL) BELTRAN<br>OUT OF OFFICE</div>
  </section>
</body>
</html>
```